New Business Card Design for Manufacturing

We are an engineering/manufacturing company that offers Advanced machining/assembly/engineering services, as well as innovative products for the heavy duty engine cooling markets.

We are looking to get a new business card designed that is clean and modern looking, but still fits the wide range of technical/skilled work we do.

- We hope to use this design as the base for other design work in new Presentations, web, and print work.

Industry/Entity Type

Engineering

Contact Information for Business Card

Our preferred color of blue is (RGB) 22/71/159 but can vary slightly from that color. Our content will be our Logo and full company name (Vantrell Forge Works, Inc.), company address, name, job title, phone number with extension, cell number, fax number, website, and email address on the cards.
We'd like the full company name next to the logo, but we are open to other interpretations of that layout.
Preferably, we would like the back side to be clean with just our logo, and the front to contain all of the contact information.

Colors
2f74b4
0355a3
85abd2

Requirements
Must have
• - Logo, company name, needed content - We are open to interpretation beyond that.
• - Standard size business card.
• - Horizontal orientation.
• - Enough space for lengthy names / job titles (for example, a job title could read "Directory of Human Resources" or "V.P. of Governmental Affairs"). We need this to look clean, whether the title be short (CEO) or long (as described above).

```html
<!DOCTYPE html>
<html lang="en">
<head>
<meta charset="utf-8">
<title>Vantrell Forge Works – Business Card</title>
<link rel="stylesheet" href="https://fonts.googleapis.com/css2?family=Signika:wght@400;600;700&family=Open+Sans:wght@400&display=swap">
<style>
  :root {
    --backdrop: #e6e6e6;
    --card-dark: #0b0b0c;
    --card-light: #f7f7f7;
    --brand-blue: #0f4d9c;
    --tagline-grey: #7d7f82;
    --text-dark: #333538;
    --rule-blue: #2a5ea8;
  }
  * { box-sizing: border-box; margin: 0; padding: 0; }
  html, body {
    width: 1200px; height: 576px; overflow: hidden;
    background: var(--backdrop);
  }
  .stage { position: relative; width: 1200px; height: 576px; }
  .card {
    position: absolute; top: 138px; width: 484px; height: 293px;
    border-radius: 12px;
  }
  .card--back { left: 82px; background: var(--card-dark); }
  .card--front { left: 602px; background: var(--card-light); }

  .wordmark {
    position: absolute; left: 0; right: 0; text-align: center;
    font-family: "Signika", sans-serif; font-weight: 700;
    letter-spacing: 1px; line-height: 1;
  }
  .tagline {
    position: absolute; left: 0; right: 0; text-align: center;
    font-family: "Signika", sans-serif; font-weight: 600;
    color: var(--tagline-grey); text-transform: uppercase; letter-spacing: 0.5px;
  }
  .card--back .wordmark { top: 98px; font-size: 62px; color: #ffffff; }
  .card--back .tagline { top: 172px; font-size: 17px; }
  .card--front .wordmark { top: 38px; font-size: 44px; color: var(--brand-blue); }
  .card--front .tagline { top: 91px; font-size: 12px; }

  .person {
    position: absolute; right: 264px; top: 146px; text-align: right;
    font-family: "Open Sans", sans-serif; color: var(--text-dark);
  }
  .person__name {
    font-family: "Signika", sans-serif; font-weight: 600;
    font-size: 21px; color: var(--brand-blue); line-height: 1.1;
  }
  .person__title { font-size: 12px; margin-top: 3px; }
  .person__address { font-size: 13px; line-height: 17px; margin-top: 14px; }

  .divider {
    position: absolute; left: 237px; top: 148px; width: 1px; height: 90px;
    background: var(--rule-blue);
  }
  .contacts {
    position: absolute; left: 260px; top: 148px; list-style: none;
    font-family: "Open Sans", sans-serif; font-size: 13px; color: var(--text-dark);
  }
  .contacts li { display: flex; align-items: center; height: 17.5px; }
  .contacts svg { width: 10px; height: 10px; margin-right: 7px; fill: var(--brand-blue); }
  .contacts .accent { color: var(--brand-blue); }

  .footer-rule {
    position: absolute; left: 22px; right: 22px; top: 256px; height: 1px;
    background: var(--rule-blue);
  }
  .company {
    position: absolute; left: 0; right: 0; top: 264px; text-align: center;
    font-family: "Signika", sans-serif; font-weight: 600; font-size: 14px;
    color: var(--brand-blue);
  }
</style>
</head>
<body>
<main class="stage">
  <section class="card card--back" aria-label="Card back">
    <div class="wordmark">VANTRELL</div>
    <div class="tagline">Built for the Long Run</div>
  </section>

  <section class="card card--front" aria-label="Card front">
    <div class="wordmark">VANTRELL</div>
    <div class="tagline">Built for the Long Run</div>

    <div class="person">
      <div class="person__name">Marla Quinn Ostby</div>
      <div class="person__title">Managing Director</div>
      <div class="person__address">78 Foundry Row, Millbrook,<br>OH 44021</div>
    </div>

    <div class="divider"></div>

    <ul class="contacts">
      <li><svg viewBox="0 0 10 10"><path d="M1 3.5C1 2 2.5 1 5 1s4 1 4 2.5L7.5 4.5 6.5 3h-3L2.5 4.5zM2 5h6l1 4H1z"/></svg>555-0142-2210 (VFW)</li>
      <li><svg viewBox="0 0 10 10"><rect x="2.5" y="0.5" width="5" height="9" rx="1"/></svg>555-0187-3391</li>
      <li><svg viewBox="0 0 10 10"><path d="M2.5 0.5h5v3h-5zM0.5 4h9v4h-2v1.5h-5V8h-2z"/></svg>555-0163-4470</li>
      <li><svg viewBox="0 0 10 10"><path d="M0.5 2h9v6h-9zM1 2.5l4 3 4-3" stroke="#f7f7f7" stroke-width="0.8"/></svg>www.<span class="accent">vantrellforge</span>.com</li>
      <li><svg viewBox="0 0 10 10"><circle cx="5" cy="5" r="4.5"/><path d="M0.5 5h9M5 0.5c-2 2.5-2 6.5 0 9M5 0.5c2 2.5 2 6.5 0 9" stroke="#f7f7f7" stroke-width="0.7" fill="none"/></svg>mostby@vantrellforge.com</li>
    </ul>

    <div class="footer-rule"></div>
    <div class="company">Vantrell Forge Works, Inc.</div>
  </section>
</main>
</body>
</html>
```